Lumavento business card

We need a modern business card - With our 4 colors - See web: www.lumavento.dk

I have attached logo and som old business Cards we have - Lets Make the new ones shine...:-) -

Industry/Entity Type

Business

Requirements
Must have
• the logo with lumavento only,

```html
<!DOCTYPE html>
<html lang="da">
<head>
<meta charset="utf-8">
<title>Lumavento – visitkort</title>
<link rel="stylesheet" href="https://fonts.googleapis.com/css2?family=Open+Sans:wght@400;600&display=swap">
<style>
  :root {
    --backdrop: #3a3a3a;
    --card: #121212;
    --card-edge: #1d1d1d;
    --lime: #a6d41f;
    --magenta: #e2177d;
    --orange: #f28c1e;
    --purple: #8a3b97;
    --soft-white: #d9d9d9;
  }
  * { margin: 0; padding: 0; box-sizing: border-box; }
  html, body { width: 1200px; height: 900px; overflow: hidden; }
  body {
    background: var(--backdrop);
    font-family: "Open Sans", sans-serif;
    position: relative;
  }
  .card {
    position: absolute;
    top: 300px;
    width: 520px;
    height: 300px;
    background: var(--card);
    border: 1px solid var(--card-edge);
    border-radius: 22px;
  }
  .card--front { left: 50px; }
  .card--back { left: 630px; }

  /* front */
  .brand-mark {
    position: absolute;
    left: 40px;
    top: 0;
    width: 190px;
    height: 300px;
    display: flex;
    flex-direction: column;
    align-items: center;
    justify-content: center;
    gap: 16px;
  }
  .brand-dot {
    width: 90px;
    height: 90px;
    border-radius: 50%;
    background: var(--lime);
  }
  .brand-name {
    color: var(--lime);
    font-size: 22px;
    font-weight: 400;
    letter-spacing: 3px;
  }
  .divider {
    position: absolute;
    left: 262px;
    top: 40px;
    width: 1px;
    height: 220px;
    background: #262626;
  }
  .contact {
    position: absolute;
    left: 285px;
    top: 50px;
    color: var(--lime);
    font-size: 14px;
    line-height: 1.3;
  }
  .person-name { font-size: 19px; font-weight: 600; }
  .person-name .first { color: var(--magenta); }
  .person-name .last { color: var(--orange); }
  .person-title { font-size: 13px; margin-bottom: 22px; }
  .address { margin-bottom: 16px; }
  .contact-list { list-style: none; }
  .contact-list li { display: flex; align-items: center; gap: 10px; margin-bottom: 4px; }
  .contact-list svg { width: 12px; height: 12px; flex: none; }

  /* back */
  .back-logo {
    position: absolute;
    left: 0; right: 0;
    top: 70px;
    display: flex;
    flex-direction: column;
    align-items: center;
  }
  .back-logo .brand-dot { width: 70px; height: 70px; margin-bottom: 12px; }
  .back-logo .brand-name { color: var(--soft-white); font-size: 20px; letter-spacing: 5px; }
  .rule {
    width: 260px;
    height: 3px;
    background: var(--lime);
    margin: 14px 0 8px;
  }
  .tagline { color: var(--soft-white); font-size: 13px; }
</style>
</head>
<body>
  <section class="card card--front">
    <div class="brand-mark">
      <div class="brand-dot"></div>
      <div class="brand-name">lumavento</div>
    </div>
    <div class="divider"></div>
    <div class="contact">
      <div class="person-name"><span class="first">Kasper</span> <span class="last">Lindholm</span></div>
      <div class="person-title">Salgsdirektor</div>
      <div class="address">Solsikkevej 14 - 8200<br>Aarhus N - Tlf. 36 47 19 02</div>
      <ul class="contact-list">
        <li>
          <svg viewBox="0 0 12 12" aria-hidden="true"><path d="M2 1h2.5l1 3-1.5 1a7 7 0 0 0 3 3l1-1.5 3 1V11a1 1 0 0 1-1 1A10 10 0 0 1 1 2a1 1 0 0 1 1-1z" fill="var(--magenta)"/></svg>
          +45 61 72 83 94
        </li>
        <li>
          <svg viewBox="0 0 12 12" aria-hidden="true"><rect x="0.5" y="2" width="11" height="8" fill="var(--orange)"/><path d="M0.5 2 6 6.5 11.5 2" stroke="var(--card)" fill="none"/></svg>
          kl@lumavento.dk
        </li>
        <li>
          <svg viewBox="0 0 12 12" aria-hidden="true"><circle cx="6" cy="6" r="5.5" fill="var(--purple)"/><path d="M0.5 6h11M6 0.5c-3 3-3 8 0 11M6 0.5c3 3 3 8 0 11" stroke="var(--card)" stroke-width="0.8" fill="none"/></svg>
          www.lumavento.dk
        </li>
      </ul>
    </div>
  </section>

  <section class="card card--back">
    <div class="back-logo">
      <div class="brand-dot"></div>
      <div class="brand-name">lumavento</div>
      <div class="rule"></div>
      <div class="tagline">Ideer der lyser</div>
    </div>
  </section>
</body>
</html>
```